Dorla's Cleaners new delivery postcard

We need to advertise for our new pick up and delivery dry cleaning/laundry service.
Mens Business Shirts $2.00
Pants $4.50
Skirts $5.00
Dry Clean Shirt/Blouse $5.00
Dress $9.00
2 Piece Suits $9.00
Updates
We would like to use a 5x7 size postcard, printed on both sides. We would like to add a discount to the card for 25% off of their first order, with the flyer.
We are a famly run dry cleaners. My name is Rosalind Tupper and my cell # is 614-302-7781. We are trying to expand our business to include free pick and delivery.
If possible can you use the logo I sent some where on the postcard? The phone # for the store is 614-295-3064.
Reason: Still need to get partners approval.

```html
<!DOCTYPE html>
<html lang="en">
<head>
<meta charset="utf-8">
<title>Dorla's Cleaners – Delivery Postcard</title>
<link rel="stylesheet" href="https://fonts.googleapis.com/css2?family=Nunito:wght@400;600;800&display=swap">
<style>
  :root {
    --bg: #ece7df;
    --paper: #ffffff;
    --band: #f1f2f4;
    --orange: #f07a1e;
    --blue: #1f8fd0;
    --navy: #2b5f9e;
    --green: #7dbb2a;
    --panel: rgba(255,255,255,0.82);
    --text-dark: #2a4f86;
  }
  * { box-sizing: border-box; margin: 0; padding: 0; }
  html, body { width: 1200px; height: 900px; overflow: hidden; }
  body {
    background: var(--bg);
    font-family: "Nunito", sans-serif;
    position: relative;
  }
  .postcard {
    position: absolute;
    width: 580px;
    height: 420px;
    background: var(--paper);
    box-shadow: 0 6px 18px rgba(0,0,0,0.25);
    overflow: hidden;
  }
  .postcard--back { left: 30px; top: 30px; }
  .postcard--front { left: 590px; top: 450px; }

  .brand {
    position: absolute;
    left: 18px; top: 14px;
    display: flex; align-items: center; gap: 8px;
    z-index: 3;
  }
  .brand__dot {
    width: 26px; height: 26px; border-radius: 50%;
    background: var(--blue);
  }
  .brand__name {
    font-size: 25px; font-weight: 600; color: var(--orange);
    letter-spacing: 0.2px;
  }

  .contact-band {
    position: absolute; left: 0; right: 0; bottom: 0; height: 62px;
    background: linear-gradient(#f7f7f8, var(--band));
    display: flex; align-items: center;
    z-index: 1;
  }
  .contact {
    display: flex; align-items: center; gap: 6px;
    font-size: 20px; color: var(--navy); font-weight: 400;
  }
  .contact svg { width: 14px; height: 14px; }

  /* back side */
  .back__header { position: absolute; left: 0; right: 0; top: 0; height: 58px; background: linear-gradient(#ffffff, #f3f4f6); }
  .back__photo {
    position: absolute; left: 10px; right: 10px; top: 58px; height: 300px;
    background: radial-gradient(circle at 22% 55%, #e6f5fb 0%, #7cc3dc 22%, #2f8fb3 48%, #135d82 75%, #0c3f60 100%);
  }
  .offer {
    position: absolute; left: 98px; top: 175px; z-index: 2;
    line-height: 1;
  }
  .offer__amount { font-size: 64px; font-weight: 800; color: var(--orange); }
  .offer__label { font-size: 34px; font-weight: 800; color: var(--blue); margin-top: 2px; }
  .offer__note { font-size: 20px; font-weight: 800; color: var(--green); margin-top: 2px; }
  .services {
    position: absolute; left: 365px; top: 150px; width: 200px; height: 215px;
    background: var(--panel); border-radius: 8px; z-index: 2;
    padding: 12px 16px;
  }
  .services__kicker { font-size: 17px; font-weight: 600; color: var(--orange); line-height: 1; }
  .services__title { font-size: 26px; font-weight: 800; color: var(--blue); line-height: 1.05; margin-bottom: 6px; }
  .services__list { list-style: none; }
  .services__list li { font-size: 17px; color: var(--navy); line-height: 1.55; }
  .services__list li::before { content: "• "; color: var(--blue); }
  .postcard--back .contact-band { padding-left: 32px; }

  /* front side */
  .front__photo {
    position: absolute; left: 0; right: 0; top: 0; height: 365px;
    background: linear-gradient(#9cc8ee 0%, #cfe4f6 48%, #8fbf52 56%, #5f9a2c 100%);
  }
  .prices {
    position: absolute; left: 32px; top: 232px; width: 215px; height: 178px;
    background: var(--panel); border-radius: 6px; z-index: 2;
    padding: 8px 10px;
  }
  .prices__row {
    display: flex; justify-content: space-between;
    font-size: 14px; color: var(--text-dark); line-height: 24.5px;
  }
  .tagline {
    position: absolute; right: 24px; top: 296px; z-index: 2;
    text-align: right; color: #ffffff; font-size: 19px; line-height: 1.2;
    text-shadow: 0 1px 3px rgba(0,0,0,0.4);
  }
  .postcard--front .contact-band { justify-content: flex-end; padding-right: 20px; }
  .postcard--front .contact { font-size: 18px; }
</style>
</head>
<body>

<section class="postcard postcard--back" aria-label="Postcard back">
  <div class="back__header"></div>
  <div class="brand">
    <span class="brand__dot"></span>
    <span class="brand__name">Dorla's Cleaners</span>
  </div>
  <div class="back__photo" role="img" aria-label="Photo of bubbles rising through clear blue water"></div>
  <div class="offer">
    <div class="offer__amount">25%</div>
    <div class="offer__label">discount</div>
    <div class="offer__note">on first order</div>
  </div>
  <div class="services">
    <div class="services__kicker">additional</div>
    <div class="services__title">Services</div>
    <ul class="services__list">
      <li>Dry cleaning</li>
      <li>Shirt laundry</li>
      <li>Alterations</li>
      <li>Wedding dresses</li>
      <li>Storage</li>
    </ul>
  </div>
  <div class="contact-band">
    <div class="contact">
      <svg viewBox="0 0 24 24" aria-hidden="true"><path fill="#7dbb2a" d="M6.6 10.8a15.1 15.1 0 0 0 6.6 6.6l2.2-2.2a1 1 0 0 1 1-.25 11.4 11.4 0 0 0 3.6.57 1 1 0 0 1 1 1V20a1 1 0 0 1-1 1A17 17 0 0 1 3 4a1 1 0 0 1 1-1h3.5a1 1 0 0 1 1 1c0 1.25.2 2.45.57 3.57a1 1 0 0 1-.25 1z"/></svg>
      <span>614-302-7781 / 614-295-3064</span>
    </div>
  </div>
</section>

<section class="postcard postcard--front" aria-label="Postcard front">
  <div class="front__photo" role="img" aria-label="Photo of white and yellow laundry drying on a clothesline over a green meadow under blue sky"></div>
  <div class="brand">
    <span class="brand__dot"></span>
    <span class="brand__name">Dorla's Cleaners</span>
  </div>
  <div class="prices">
    <div class="prices__row"><span>Mens Business Shirts</span><span>$2.00</span></div>
    <div class="prices__row"><span>Pants</span><span>$4.50</span></div>
    <div class="prices__row"><span>Skirts</span><span>$5.00</span></div>
    <div class="prices__row"><span>Dry Clean Shirt/Blouse</span><span>$5.00</span></div>
    <div class="prices__row"><span>Dress</span><span>$9.00</span></div>
    <div class="prices__row"><span>2 Piece Suits</span><span>$9.00</span></div>
  </div>
  <div class="tagline">free pick up and delivery<br>dry cleaning/laundry</div>
  <div class="contact-band">
    <div class="contact">
      <svg viewBox="0 0 24 24" aria-hidden="true"><path fill="#7dbb2a" d="M6.6 10.8a15.1 15.1 0 0 0 6.6 6.6l2.2-2.2a1 1 0 0 1 1-.25 11.4 11.4 0 0 0 3.6.57 1 1 0 0 1 1 1V20a1 1 0 0 1-1 1A17 17 0 0 1 3 4a1 1 0 0 1 1-1h3.5a1 1 0 0 1 1 1c0 1.25.2 2.45.57 3.57a1 1 0 0 1-.25 1z"/></svg>
      <span>614-302-7781 / 614-295-3064</span>
    </div>
  </div>
</section>

</body>
</html>
```